KLV Plant Services

We are a heavy diesel mechanical business with additional air con certificates, remapping engine rebuilt

Contact Information for Business Card

Company Name, Director Name, Managing Director, Contact details, email and website

Font styles to use
Serif
Script

```html
<!DOCTYPE html>
<html lang="en">
<head>
<meta charset="utf-8">
<title>KLV Plant Services — Business Card</title>
<link rel="stylesheet" href="https://fonts.googleapis.com/css2?family=Lora:wght@400;600&family=Great+Vibes&display=swap">
<style>
  :root {
    --page: #e6e7eb;
    --card: #ffffff;
    --card-shade: #f1f1f3;
    --navy: #2a2c7c;
    --band: #2f3e8e;
    --band-light: #4453a3;
    --ink-soft: #5f6168;
    --arm: #d9d9dc;
    --arm-light: #ececee;
    --shadow: rgba(20, 22, 40, 0.18);
  }
  * { box-sizing: border-box; margin: 0; padding: 0; }
  html, body {
    width: 1200px; height: 900px; overflow: hidden;
    background: var(--page);
    font-family: "Lora", serif;
  }
  .canvas { position: relative; width: 1200px; height: 900px; }
  .card {
    position: absolute; left: 290px;
    width: 620px; height: 354px;
    background: linear-gradient(160deg, var(--card) 40%, var(--card-shade));
    box-shadow: 0 10px 28px var(--shadow);
    overflow: hidden;
  }
  .card--front { top: 70px; }
  .card--back { top: 476px; }
  .band { position: absolute; left: 0; bottom: 0; width: 100%; height: 100%; }

  .arm-art {
    position: absolute;
    background: linear-gradient(180deg, var(--arm-light), var(--arm));
    opacity: 0.75;
    border-radius: 6px;
  }
  .card--front .arm-art { left: 150px; top: 0; width: 150px; height: 300px; }
  .card--back .arm-art { left: 130px; top: 0; width: 150px; height: 320px; }

  /* Front */
  .front-name {
    position: absolute; right: 66px; top: 40px;
    color: var(--navy); font-weight: 600;
  }
  .front-name__initials { display: block; font-size: 104px; line-height: 1; letter-spacing: 2px; }
  .front-name__rest { display: block; font-size: 32px; line-height: 1.1; }

  /* Back */
  .back-name {
    position: absolute; right: 48px; top: 36px;
    display: flex; align-items: center; gap: 12px;
  }
  .back-name__dot {
    width: 40px; height: 40px; border-radius: 50%;
    border: 3px solid var(--navy);
  }
  .back-name__text { color: var(--navy); font-weight: 600; font-size: 26px; line-height: 1.1; }
  .person { position: absolute; left: 40px; top: 142px; }
  .person__name { color: var(--navy); font-size: 19px; font-weight: 400; letter-spacing: 1px; }
  .person__role {
    color: var(--ink-soft); font-family: "Great Vibes", cursive;
    font-size: 20px; line-height: 1.1; margin-top: 2px;
  }
  .contacts {
    list-style: none; margin-top: 14px;
    color: var(--ink-soft); font-size: 13px; font-weight: 400;
  }
  .contacts li { display: flex; align-items: center; gap: 9px; height: 22px; }
  .contacts svg { width: 14px; height: 14px; fill: var(--navy); flex: none; }
  .address {
    position: absolute; left: 320px; top: 142px;
    padding-left: 14px; border-left: 1.5px solid var(--navy);
    color: var(--ink-soft); font-size: 13px; line-height: 1.55; font-style: normal;
  }
</style>
</head>
<body>
<main class="canvas">

  <section class="card card--front" aria-label="Business card front">
    <div class="arm-art" role="img" aria-label="Faint grey illustration of an excavator arm and bucket"></div>
    <svg class="band" viewBox="0 0 620 354" preserveAspectRatio="none" aria-hidden="true">
      <path fill="var(--band)" d="M0 318 L40 314 L70 318 L110 312 L150 304 L200 296 L240 282 L280 274 L320 262 L350 250 L390 246 L420 232 L450 214 L480 204 L520 196 L550 180 L580 176 L620 168 L620 354 L0 354 Z"/>
      <path fill="var(--band-light)" opacity="0.35" d="M0 326 L60 322 L130 318 L210 304 L300 284 L380 262 L450 230 L520 210 L620 186 L620 200 L520 224 L440 246 L360 276 L260 300 L150 328 L0 340 Z"/>
    </svg>
    <h1 class="front-name">
      <span class="front-name__initials">KLV</span>
      <span class="front-name__rest">Plant Services</span>
    </h1>
  </section>

  <section class="card card--back" aria-label="Business card back">
    <div class="arm-art" role="img" aria-label="Faint grey illustration of an excavator arm and bucket"></div>
    <svg class="band" viewBox="0 0 620 354" preserveAspectRatio="none" aria-hidden="true">
      <path fill="var(--band)" d="M0 330 L40 326 L80 328 L120 324 L170 318 L210 312 L250 304 L290 296 L330 288 L360 278 L390 268 L420 256 L450 246 L480 234 L510 222 L540 212 L580 204 L620 196 L620 354 L0 354 Z"/>
      <path fill="var(--band-light)" opacity="0.35" d="M0 338 L90 334 L180 324 L270 306 L360 282 L450 256 L540 226 L620 210 L620 222 L530 242 L440 270 L340 298 L230 322 L120 340 L0 348 Z"/>
    </svg>

    <div class="back-name">
      <span class="back-name__dot" aria-hidden="true"></span>
      <span class="back-name__text">KLV<br>Plant Services</span>
    </div>

    <div class="person">
      <p class="person__name">DALE MORGAN</p>
      <p class="person__role">Managing Director</p>
      <ul class="contacts">
        <li>
          <svg viewBox="0 0 24 24" aria-hidden="true"><path d="M6.6 10.8a15.1 15.1 0 0 0 6.6 6.6l2.2-2.2a1 1 0 0 1 1-.25 11.4 11.4 0 0 0 3.6.57 1 1 0 0 1 1 1V20a1 1 0 0 1-1 1A17 17 0 0 1 3 4a1 1 0 0 1 1-1h3.5a1 1 0 0 1 1 1c0 1.25.2 2.45.57 3.57a1 1 0 0 1-.25 1z"/></svg>
          0400 123 456
        </li>
        <li>
          <svg viewBox="0 0 24 24" aria-hidden="true"><path d="M2 5h20v14H2z"/><path d="M3 6l9 7 9-7" fill="none" stroke="#fff" stroke-width="1.6"/></svg>
          admin@klvplantservices.net
        </li>
        <li>
          <svg viewBox="0 0 24 24" aria-hidden="true"><circle cx="12" cy="12" r="9.5" fill="none" stroke="var(--navy)" stroke-width="1.6"/><ellipse cx="12" cy="12" rx="4" ry="9.5" fill="none" stroke="var(--navy)" stroke-width="1.4"/><path d="M3 12h18M5 7h14M5 17h14" stroke="var(--navy)" stroke-width="1.2"/></svg>
          www.klvplantservices.net
        </li>
      </ul>
    </div>

    <address class="address">
      48 Foundry Road<br>
      Ridgeview, WA 6000, Australia
    </address>
  </section>

</main>
</body>
</html>
```